New York City Sponsorship Page with Click Through Supporting Pages

Metro Talent Circle, the leading New York City resource for HR Professionals is a membership organization with almost 2,000 individual members.

We need section/page(s) created for our current sponsorship offerings. Our platform is on ClubLedger Platform and we need capability to edit the page, etc. It must be HTML ready/coded.

Attached is the mock up of how we want the page to look (pages mockup pdf) as well as each of the categories which should be included (in the excel files). Our current page is here: http://www.metrotalentcircle.example/?page=sponsors and is not easy to read through. We want something that is visually appealing and clean but showcases all of the different ways to sponsor the Chapter.

Additionally, we are taking the information from this page and turning it into a brochure.

Target Market(s)

New York City Companies who have HR Professionals or services they want to attract or offer.

Coding

Coded - Design and coding required

Number of Pages Required

5+ page

Requirements
Must have
• Clean Look and feel, easy functionality, necessary information and purchases. Match the top navigation of current page. Opportunity for current sponsor logos to be highlighted on the page. Easy to update/maintain.
Nice to have
• Option to pay for sponsorships through the page using our credit card processor.
Should not have
• Overwhelming text in sections

```html
<!DOCTYPE html>
<html lang="en">
<head>
<meta charset="utf-8">
<title>Sponsorship Opportunities – Metro Talent Circle</title>
<link href="https://fonts.googleapis.com/css2?family=Open+Sans:wght@400;600;700;800&display=swap" rel="stylesheet">
<style>
:root{
  --navy:#1b2a45;
  --navy-deep:#142036;
  --blue:#1a7fc1;
  --red:#d21f2b;
  --graphite:#3b4250;
  --ink:#2a2f38;
  --muted:#6b7280;
  --line:#dfe3e8;
  --band:#eef0f3;
  --white:#ffffff;
}
*{box-sizing:border-box;margin:0;padding:0}
html,body{width:835px;height:1200px;overflow:hidden}
body{font-family:"Open Sans",Arial,sans-serif;color:var(--ink);background:var(--white);position:relative}

/* header + hero */
.hero{position:relative;height:235px;background:linear-gradient(180deg,#0d1322 0%,#1c2740 45%,#3a3240 75%,#1a1f2d 100%)}
.hero-image{position:absolute;left:0;right:0;top:70px;bottom:0;background:linear-gradient(90deg,#151b2b 0%,#2c3552 30%,#4a3f4a 55%,#263049 80%,#121826 100%);opacity:.9}
.brand{position:absolute;left:22px;top:0;width:178px;height:66px;background:var(--white);display:flex;align-items:center;gap:8px;padding:0 12px}
.brand-mark{width:14px;height:14px;background:var(--red)}
.brand-name{font-weight:800;font-size:15px;line-height:1.05;color:var(--red)}
.utility{position:absolute;right:22px;top:10px;display:flex;align-items:center;gap:12px;font-size:9px;color:#cfd5df;text-transform:uppercase;letter-spacing:.4px}
.search{width:110px;height:16px;background:var(--white);border-radius:2px;font-size:8px;color:#9aa0a8;padding:2px 6px;text-transform:none}
.nav{position:absolute;left:225px;top:44px;display:flex;gap:20px;font-size:10.5px;color:var(--white);font-weight:600}

/* breadcrumb */
.breadcrumb{height:36px;border-bottom:1px solid var(--line);font-size:8.5px;color:var(--muted);padding:14px 50px 0;text-transform:uppercase;letter-spacing:.3px}

/* intro */
.intro{text-align:center;padding-top:30px;height:250px}
.intro-title{display:flex;justify-content:center;align-items:center;gap:10px;font-size:21px;font-weight:800;color:var(--navy);letter-spacing:.5px}
.intro-title span{color:var(--red)}
.intro-icon{width:30px;height:30px}
.intro-text{font-size:10.5px;color:var(--ink);margin-top:22px;line-height:1.5}
.intro-text p+p{margin-top:14px}
.divider{width:500px;height:1px;background:var(--line);margin:48px auto 0}
.choose{font-size:16px;font-weight:700;color:var(--navy);margin-top:34px}
.choose span{color:var(--red)}

/* cards */
.cards{display:flex;gap:14px;padding:0 50px;margin-top:22px}
.card{width:173px;height:182px;position:relative;background:var(--white);border:1px solid var(--line)}
.card-head{height:62px;display:flex;align-items:center;gap:8px;padding:0 10px;color:var(--white);font-weight:700;font-size:11.5px;line-height:1.25}
.card-icon{flex:none;width:34px;height:34px;border-radius:50%;background:var(--white);display:flex;align-items:center;justify-content:center}
.card-body{font-size:8.5px;line-height:1.45;color:var(--ink);padding:10px 12px;text-align:center}
.price{position:absolute;left:50%;bottom:12px;transform:translateX(-50%);width:86px;height:24px;border-radius:3px;color:var(--white);font-weight:700;font-size:12px;display:flex;align-items:center;justify-content:center}
.is-navy .card-head,.is-navy .price{background:var(--navy)}
.is-blue .card-head,.is-blue .price{background:var(--blue)}
.is-red .card-head,.is-red .price{background:var(--red)}
.is-graphite .card-head,.is-graphite .price{background:var(--graphite)}

/* calls to action */
.actions{display:flex;justify-content:center;gap:24px;margin-top:52px}
.action{display:flex;align-items:center;width:220px;height:52px}
.action-icon{width:52px;height:52px;border-radius:50%;border:3px solid var(--white);display:flex;align-items:center;justify-content:center;position:relative;z-index:1;box-shadow:0 0 0 1px var(--line)}
.action-label{flex:1;height:40px;margin-left:-14px;padding-left:22px;display:flex;align-items:center;color:var(--white);font-size:9.5px;font-weight:700;line-height:1.25;border-radius:0 4px 4px 0}
.a-navy .action-icon,.a-navy .action-label{background:var(--navy)}
.a-blue .action-icon,.a-blue .action-label{background:var(--blue)}
.a-red .action-icon,.a-red .action-label{background:var(--red)}

/* sponsors */
.sponsors{position:absolute;left:0;right:0;top:880px;height:188px;background:var(--band);padding:24px 50px 0}
.sponsors-title{text-align:center;font-size:16px;font-weight:700;color:var(--navy)}
.sponsors-title span{color:var(--red)}
.tiers{display:flex;gap:70px;margin-top:22px;padding-left:10px}
.tier-label{font-size:11px;font-weight:700;color:var(--navy);margin-bottom:12px}
.tier-logos{display:flex;align-items:center;gap:26px}
.sponsor{display:flex;align-items:center;gap:6px;font-size:15px;font-weight:700;color:var(--navy)}
.sponsor i{width:10px;height:10px;background:var(--navy);display:block}

/* footer */
.footer{position:absolute;left:0;right:0;top:1068px;height:132px;background:var(--navy);color:#c9d1de;display:flex;padding:16px 50px 0;gap:38px}
.f-col h4{color:var(--white);font-size:11px;font-weight:600;margin-bottom:6px}
.f-col li{list-style:none;font-size:8.5px;line-height:1.5}
.f-nav{width:110px}
.f-contact{width:150px;font-size:8.5px;line-height:1.6}
.badge{width:130px;height:84px;background:#2a3b5c;border:2px solid #c9d1de}
.f-social{margin-left:auto}
.social-row{display:flex;gap:6px}
.social-row i{width:16px;height:16px;background:var(--blue);display:block;border-radius:2px}
.legal{position:absolute;left:0;right:0;bottom:0;height:18px;background:var(--navy-deep);font-size:7.5px;color:#9aa5b8;text-align:center;line-height:18px}
</style>
</head>
<body>

<header class="hero">
  <div class="hero-image" role="img" aria-label="New York City skyline at night"></div>
  <div class="brand"><span class="brand-mark"></span><span class="brand-name">Metro Talent<br>Circle</span></div>
  <div class="utility"><span>Contact Us</span><span>Membership</span><span>Login</span><span class="search">Search</span></div>
  <nav class="nav"><span>Our New Website</span><span>About Us</span><span>Membership</span><span>Events</span><span>Sponsorships</span><span>Career Center</span><span>HR Resources</span></nav>
</header>

<div class="breadcrumb">Sponsorships &nbsp;›&nbsp; Sponsorship Opportunities</div>

<section class="intro">
  <h1 class="intro-title">
    <svg class="intro-icon" viewBox="0 0 30 30"><circle cx="15" cy="15" r="14" fill="none" stroke="#1b2a45" stroke-width="2"/><path d="M8 12h14v10H8z" fill="none" stroke="#d21f2b" stroke-width="2"/><path d="M8 12l7 5 7-5" fill="none" stroke="#d21f2b" stroke-width="2"/></svg>
    INVITATION FOR <span>SPONSORS</span>
  </h1>
  <div class="intro-text">
    <p>Thank you for your interest in Metro Talent Circle.</p>
    <p>As a premier HR chapter, we offer many opportunities to increase your exposure to the New York HR community.</p>
  </div>
  <div class="divider"></div>
  <h2 class="choose">Choose the sponsorship category <span>that best meets your needs:</span></h2>
</section>

<section class="cards">
  <article class="card is-navy">
    <div class="card-head"><span class="card-icon"><svg width="18" height="18" viewBox="0 0 18 18"><path d="M9 1l2.4 5 5.4.6-4 3.7 1.1 5.4L9 13l-4.9 2.7 1.1-5.4-4-3.7 5.4-.6z" fill="#1b2a45"/></svg></span>Strategic<br>Partnership</div>
    <p class="card-body">Opportunities for a strategic sponsorship, at different levels, each providing a valuable set of great benefits.</p>
    <div class="price">$3,500+</div>
  </article>
  <article class="card is-blue">
    <div class="card-head"><span class="card-icon"><svg width="18" height="18" viewBox="0 0 18 18"><rect x="2" y="4" width="14" height="12" fill="none" stroke="#1a7fc1" stroke-width="2"/><path d="M2 8h14M6 2v4M12 2v4" stroke="#1a7fc1" stroke-width="2"/></svg></span>Programs /<br>Events</div>
    <p class="card-body">Opportunities to sponsor a wide range of events, from all day conferences to hour sessions etc.</p>
    <div class="price">$500+</div>
  </article>
  <article class="card is-red">
    <div class="card-head"><span class="card-icon"><svg width="18" height="18" viewBox="0 0 18 18"><path d="M2 7h4l8-4v12l-8-4H2z" fill="#d21f2b"/><path d="M5 11l1 5h2l-1-5" fill="#d21f2b"/></svg></span>Advertising /<br>Promotion</div>
    <p class="card-body">Opportunities for regular online and digital sponsoring in form of website banners, website ads, e-blasts etc.</p>
    <div class="price">$150+</div>
  </article>
  <article class="card is-graphite">
    <div class="card-head"><span class="card-icon"><svg width="18" height="18" viewBox="0 0 18 18"><circle cx="9" cy="9" r="3" fill="none" stroke="#3b4250" stroke-width="2"/><path d="M9 1v3M9 14v3M1 9h3M14 9h3M3.3 3.3l2.1 2.1M12.6 12.6l2.1 2.1M3.3 14.7l2.1-2.1M12.6 5.4l2.1-2.1" stroke="#3b4250" stroke-width="2"/></svg></span>Custom</div>
    <p class="card-body">Build your own sponsorship program from our variety of opportunities.</p>
    <div class="price">$250+</div>
  </article>
</section>

<section class="actions">
  <a class="action a-navy"><span class="action-icon"><svg width="22" height="18" viewBox="0 0 22 18"><rect x="1" y="1" width="20" height="16" fill="none" stroke="#fff" stroke-width="2"/><path d="M1 1l10 8 10-8" fill="none" stroke="#fff" stroke-width="2"/></svg></span><span class="action-label">More about our<br>sponsorship packages</span></a>
  <a class="action a-blue"><span class="action-icon"><svg width="20" height="20" viewBox="0 0 20 20"><rect x="2" y="4" width="16" height="14" fill="none" stroke="#fff" stroke-width="2"/><path d="M2 8h16M6 2v4M14 2v4M7 13l2 2 4-4" fill="none" stroke="#fff" stroke-width="2"/></svg></span><span class="action-label">Book your<br>sponsorship packages</span></a>
  <a class="action a-red"><span class="action-icon"><svg width="20" height="20" viewBox="0 0 20 20"><path d="M4 2l4 1 1 4-2 2a11 11 0 005 5l2-2 4 1 1 4-2 1C9 18 2 11 2 4z" fill="#fff"/></svg></span><span class="action-label">Contact our<br>sponsorship team</span></a>
</section>

<section class="sponsors">
  <h2 class="sponsors-title">Thanks to <span>our sponsors</span></h2>
  <div class="tiers">
    <div class="tier">
      <div class="tier-label">Gold</div>
      <div class="tier-logos">
        <span class="sponsor">Harlow Bennett</span>
        <span class="sponsor"><i></i>Transit Perks Group</span>
      </div>
    </div>
    <div class="tier">
      <div class="tier-label">Silver</div>
      <div class="tier-logos">
        <span class="sponsor"><i></i>Keystone Benefits</span>
        <span class="sponsor">Brightforce</span>
      </div>
    </div>
  </div>
</section>

<footer class="footer">
  <div class="f-col f-nav">
    <h4>Navigation</h4>
    <ul><li>About Us</li><li>Membership</li><li>Events</li><li>Career Center</li><li>Sponsorships</li><li>HR Resources</li></ul>
  </div>
  <div class="f-col f-contact">
    <h4>Contact Us</h4>
    Phone: 212-555-0142<br>Fax: 212-555-0143<br>info@metrotalentcircle.example
  </div>
  <div class="badge" role="img" aria-label="Affiliate badge"></div>
  <div class="f-col f-social">
    <h4>Connect With Us</h4>
    <div class="social-row"><i></i><i></i><i></i><i></i><i></i></div>
  </div>
  <div class="legal">Membership Software Powered by ClubLedger® &nbsp;::&nbsp; Legal</div>
</footer>

</body>
</html>
```